BildeVOLD buisnesscard

Hey :) I need a modern buisnesscard for my company BildeVOLD
It most have:
Dagligleder og Fotograf: Henrik Audun Strandvik

Mob: +4791264085
Epost: post@bildevold.example
Adresse: Kvernbakken9, 6040 Langevåg

Facbook and instagram logo with text BildeVOLD

BildeVOLD logo

It Company

```html
<!DOCTYPE html>
<html lang="no">
<head>
<meta charset="utf-8">
<title>BildeVOLD – visittkort</title>
<link href="https://fonts.googleapis.com/css2?family=Montserrat:wght@400;500;700;800&display=swap" rel="stylesheet">
<style>
  :root {
    --bg: #d9d9d9;
    --card-dark: #050505;
    --card-light: #ffffff;
    --mark-grey: #b1b1b1;
    --name-grey: #a9a9a9;
    --ink: #1a1a1a;
    --soft-white: #e6e6e6;
  }
  * { margin: 0; padding: 0; box-sizing: border-box; }
  html, body { width: 1200px; height: 900px; overflow: hidden; }
  body {
    background: var(--bg);
    font-family: "Montserrat", sans-serif;
    position: relative;
  }
  .card {
    position: absolute;
    width: 540px;
    height: 310px;
    border-radius: 18px;
    box-shadow: 0 10px 28px rgba(0,0,0,.25);
    overflow: hidden;
  }
  /* Back side */
  .card-back {
    left: 110px; top: 120px;
    background: var(--card-dark);
  }
  .back-brand {
    position: absolute;
    left: 0; right: 0; top: 122px;
    text-align: center;
    font-size: 50px;
    font-weight: 800;
    color: var(--mark-grey);
    letter-spacing: -1px;
  }
  .back-social {
    position: absolute;
    right: 26px; bottom: 104px;
    display: flex; flex-direction: column; align-items: flex-end; gap: 6px;
  }
  .social-square {
    width: 12px; height: 12px;
    background: var(--soft-white);
    border-radius: 2px;
  }
  .social-handle {
    font-size: 13px;
    font-weight: 400;
    color: var(--soft-white);
  }
  /* Front side */
  .card-front {
    left: 550px; top: 470px;
    background: var(--card-light);
  }
  .front-brand {
    position: absolute;
    right: 40px; top: 54px;
    font-size: 34px;
    font-weight: 800;
    color: var(--mark-grey);
    letter-spacing: -0.5px;
  }
  .cut-line {
    position: absolute;
    left: 30px; top: 0;
    width: 2px; height: 310px;
  }
  .details {
    position: absolute;
    left: 62px; top: 166px;
  }
  .person-name {
    font-size: 20px;
    font-weight: 500;
    color: var(--name-grey);
    letter-spacing: .5px;
  }
  .person-role {
    font-size: 14px;
    color: var(--ink);
    margin-top: 4px;
    margin-bottom: 14px;
  }
  .contact-list { list-style: none; }
  .contact-item {
    display: flex; align-items: center; gap: 10px;
    font-size: 15px;
    color: var(--ink);
    line-height: 21px;
  }
  .contact-icon { width: 10px; height: 10px; flex: none; }
</style>
</head>
<body>

  <section class="card card-back" aria-label="Visittkort bakside">
    <div class="back-brand">BildeVOLD</div>
    <div class="back-social">
      <span class="social-square"></span>
      <span class="social-handle">BildeVOLD</span>
    </div>
  </section>

  <section class="card card-front" aria-label="Visittkort forside">
    <div class="front-brand">BildeVOLD</div>

    <svg class="cut-line" viewBox="0 0 2 310" preserveAspectRatio="none">
      <line x1="1" y1="0" x2="1" y2="310" stroke="#111" stroke-width="2" stroke-dasharray="8 5"/>
    </svg>

    <div class="details">
      <div class="person-name">Henrik Audun Strandvik</div>
      <div class="person-role">Dagligleder og Fotograf</div>
      <ul class="contact-list">
        <li class="contact-item">
          <svg class="contact-icon" viewBox="0 0 10 10"><path d="M2 1 L4 1 L4.6 3 L3.4 3.8 Q4.4 5.8 6.2 6.6 L7 5.4 L9 6 L9 8 Q5 9 2.5 6 Q1 4 2 1Z" fill="#888"/></svg>
          <span>+4791264085</span>
        </li>
        <li class="contact-item">
          <svg class="contact-icon" viewBox="0 0 10 10"><rect x="0.5" y="2" width="9" height="6" fill="none" stroke="#888"/><path d="M0.5 2 L5 5.5 L9.5 2" fill="none" stroke="#888"/></svg>
          <span>post@bildevold.example</span>
        </li>
        <li class="contact-item">
          <svg class="contact-icon" viewBox="0 0 10 10"><path d="M5 0.5 A3.3 3.3 0 0 1 8.3 3.8 Q8.3 6 5 9.5 Q1.7 6 1.7 3.8 A3.3 3.3 0 0 1 5 0.5Z" fill="#888"/><circle cx="5" cy="3.8" r="1.2" fill="#fff"/></svg>
          <span>Kvernbakken9, 6040 Langevåg</span>
        </li>
      </ul>
    </div>
  </section>

</body>
</html>
```